Powerpoint template

I am looking for a brand based PPT template that can also be used as the basis for datasheet creation. I have attached a document with some of our branding structure in as an FYI to help.

To be clear I am looking a background design, bullets, layouts, different styles for differing content types. This is a template to be used for lots of presentations.

Reason: I have committed to the payment and wanted to give people chance to respond.

Target Market(s)

Enterprise

Requirements
Must have
• Brand standard. different page design choices for different content types
Nice to have
• brand font if it works. Use of some play on the logo in bullets
Should not have
• must be on brand and focused on the business audience

```html
<!DOCTYPE html>
<html lang="en">
<head>
<meta charset="utf-8">
<title>Project Title Here</title>
<link rel="stylesheet" href="https://fonts.googleapis.com/css2?family=Ubuntu:wght@400;500&family=Arimo:wght@400&display=swap">
<style>
  :root {
    --bg: #f0f0f0;
    --brand-blue: #1f75bb;
    --brand-green: #8cc63f;
    --footer-blue: #1c6aa8;
    --text-dark: #333333;
    --white: #ffffff;
  }
  * { margin: 0; padding: 0; box-sizing: border-box; }
  html, body { width: 1200px; height: 900px; overflow: hidden; background: var(--bg); }
  .slide {
    position: relative;
    width: 1200px;
    height: 900px;
    background: var(--bg);
    overflow: hidden;
  }
  .slide-title {
    position: absolute;
    left: 33px;
    top: 28px;
    font-family: "Ubuntu", sans-serif;
    font-weight: 400;
    font-size: 44px;
    letter-spacing: 0.5px;
  }
  .slide-title .title-lead { color: var(--brand-blue); }
  .slide-title .title-rest { color: var(--brand-green); }

  .brand {
    position: absolute;
    right: 14px;
    top: 36px;
    display: flex;
    align-items: center;
    gap: 12px;
  }
  .brand-dot {
    width: 34px;
    height: 34px;
    border-radius: 50%;
    background: var(--brand-blue);
  }
  .brand-name {
    font-family: "Ubuntu", sans-serif;
    font-weight: 400;
    font-size: 44px;
    color: var(--brand-blue);
    line-height: 1;
  }

  .header-rule {
    position: absolute;
    left: 0;
    width: 1200px;
  }
  .header-rule.blue { top: 118px; height: 2px; background: var(--brand-blue); }
  .header-rule.green { top: 124px; height: 2px; background: var(--brand-green); }

  .bullet-list {
    position: absolute;
    left: 78px;
    top: 220px;
    list-style: none;
  }
  .bullet-list li {
    display: flex;
    align-items: center;
    height: 69px;
    font-family: "Arimo", sans-serif;
    font-size: 22.5px;
    color: var(--text-dark);
    white-space: nowrap;
  }
  .bullet-icon {
    width: 20px;
    height: 28px;
    margin-right: 19px;
    flex: none;
  }

  .footer-bar {
    position: absolute;
    left: 0;
    bottom: 0;
    width: 860px;
    height: 12px;
    background: var(--brand-green);
  }
  .footer-tab {
    position: absolute;
    right: 0;
    bottom: 0;
    width: 1200px;
    height: 42px;
  }
  .footer-url {
    position: absolute;
    right: 42px;
    bottom: 8px;
    font-family: "Arimo", sans-serif;
    font-size: 20px;
    letter-spacing: 2.6px;
    color: var(--white);
  }
</style>
</head>
<body>
<main class="slide">
  <h1 class="slide-title"><span class="title-lead">Project</span> <span class="title-rest">Title Here</span></h1>

  <div class="brand">
    <span class="brand-dot"></span>
    <span class="brand-name">veranode</span>
  </div>

  <div class="header-rule blue"></div>
  <div class="header-rule green"></div>

  <ul class="bullet-list">
    <li><svg class="bullet-icon" viewBox="0 0 20 28"><polyline points="5,4 15,14 5,24" fill="none" stroke="#8cc63f" stroke-width="5" stroke-linecap="round" stroke-linejoin="round"/></svg>Subtext here Subtext here Subtext here Subtext here Subtext here Subtext here Subtext here</li>
    <li><svg class="bullet-icon" viewBox="0 0 20 28"><polyline points="5,4 15,14 5,24" fill="none" stroke="#8cc63f" stroke-width="5" stroke-linecap="round" stroke-linejoin="round"/></svg>Subtext here Subtext here Subtext here Subtext here Subtext here Subtext here Subtext here</li>
    <li><svg class="bullet-icon" viewBox="0 0 20 28"><polyline points="5,4 15,14 5,24" fill="none" stroke="#8cc63f" stroke-width="5" stroke-linecap="round" stroke-linejoin="round"/></svg>Subtext here Subtext here Subtext here Subtext here Subtext here Subtext here Subtext here</li>
    <li><svg class="bullet-icon" viewBox="0 0 20 28"><polyline points="5,4 15,14 5,24" fill="none" stroke="#8cc63f" stroke-width="5" stroke-linecap="round" stroke-linejoin="round"/></svg>Subtext here Subtext here Subtext here Subtext here Subtext here Subtext here Subtext here</li>
    <li><svg class="bullet-icon" viewBox="0 0 20 28"><polyline points="5,4 15,14 5,24" fill="none" stroke="#8cc63f" stroke-width="5" stroke-linecap="round" stroke-linejoin="round"/></svg>Subtext here Subtext here Subtext here Subtext here Subtext here Subtext here Subtext here</li>
    <li><svg class="bullet-icon" viewBox="0 0 20 28"><polyline points="5,4 15,14 5,24" fill="none" stroke="#8cc63f" stroke-width="5" stroke-linecap="round" stroke-linejoin="round"/></svg>Subtext here Subtext here Subtext here Subtext here Subtext here Subtext here Subtext here</li>
    <li><svg class="bullet-icon" viewBox="0 0 20 28"><polyline points="5,4 15,14 5,24" fill="none" stroke="#8cc63f" stroke-width="5" stroke-linecap="round" stroke-linejoin="round"/></svg>Subtext here Subtext here Subtext here Subtext here Subtext here Subtext here Subtext here</li>
    <li><svg class="bullet-icon" viewBox="0 0 20 28"><polyline points="5,4 15,14 5,24" fill="none" stroke="#8cc63f" stroke-width="5" stroke-linecap="round" stroke-linejoin="round"/></svg>Subtext here Subtext here Subtext here Subtext here Subtext here Subtext here Subtext here</li>
  </ul>

  <div class="footer-bar"></div>
  <svg class="footer-tab" viewBox="0 0 1200 42" preserveAspectRatio="none">
    <polygon points="840,0 1200,0 1200,42 822,42" fill="#1c6aa8"/>
  </svg>
  <p class="footer-url">www.veranode.com</p>
</main>
</body>
</html>
```